Financial Services General Marketing Brochure

Need a brochure to help recipients understand what makes BWC unique and the services that we offer. Must match look/feel of website https://brightwellcustody.example Layouts should make it easy to read the content - content should not be crammed into a traditional size/layout. Please see attached creative brief for specifics.

Target Market(s)

Financial advisors and mature couples looking for trustee services.

Industry/Entity Type

Financial Service

Colors
34a7d8
ffc214

Requirements
Must have
• See Creative Brief

```html
<!DOCTYPE html>
<html lang="en">
<head>
<meta charset="utf-8">
<title>BWC Brochure Spread</title>
<link href="https://fonts.googleapis.com/css2?family=Merriweather:ital,wght@0,300;0,400;1,300;1,400&family=Open+Sans:wght@400;600&display=swap" rel="stylesheet">
<style>
  :root {
    --page: #ffffff;
    --frame: #b9b9b9;
    --slate: #56728f;
    --slate-text: #4e6b88;
    --body: #555555;
    --cream: #f8f3ed;
    --gold: #f1b84a;
    --tan: #cdb79e;
    --photo-office: #5f5a52;
    --photo-warm: #e9ddd0;
  }
  * { margin: 0; padding: 0; box-sizing: border-box; }
  html, body { width: 1200px; height: 1000px; overflow: hidden; background: var(--page); }
  .canvas { position: relative; width: 1200px; height: 1000px; font-family: "Open Sans", sans-serif; color: var(--body); }
  .spread { position: absolute; left: 0; top: 199px; width: 1200px; height: 602px; border: 2px solid var(--frame); }
  .panel-right { position: absolute; left: 600px; top: 201px; width: 598px; height: 598px; background: var(--cream); }
  .fold { position: absolute; left: 599px; top: 180px; height: 640px; border-left: 2px dashed var(--frame); }
  .portrait { position: absolute; left: 2px; top: 201px; width: 298px; height: 165px;
    background: linear-gradient(120deg, #8d8a82 0%, var(--photo-office) 45%, #2f3f5e 100%); }
  .title-bar { position: absolute; left: 300px; top: 234px; width: 299px; height: 65px; background: var(--slate);
    color: #fff; font-family: "Merriweather", serif; font-weight: 300; font-size: 20px; line-height: 65px; padding-left: 17px; }
  .intro { position: absolute; left: 43px; top: 404px; width: 222px; font-size: 11.4px; line-height: 17.3px; }
  .intro p + p { margin-top: 17px; }
  .dropcap { float: left; font-family: "Merriweather", serif; font-size: 50px; line-height: 40px; color: var(--slate-text); margin: 2px 2px 0 0; }
  .signature { position: absolute; left: 95px; top: 736px; font-size: 13px; line-height: 18px; }
  .signature strong { font-weight: 600; color: #444; display: block; }
  .qualities { position: absolute; left: 326px; top: 333px; width: 252px; }
  .quality h3 { font-family: "Merriweather", serif; font-style: italic; font-weight: 300; font-size: 15px; color: var(--slate-text); margin-bottom: 4px; }
  .quality p { font-size: 10.6px; line-height: 15.2px; }
  .quality + .quality { margin-top: 11px; }
  .band { position: absolute; left: 600px; top: 234px; width: 598px; height: 65px; background: var(--gold); color: #fff; text-align: center; font-family: "Merriweather", serif; font-weight: 300; }
  .band .org { font-family: "Open Sans", sans-serif; font-size: 17px; margin-top: 9px; letter-spacing: .3px; }
  .band .team { font-size: 20px; margin-top: 1px; }
  .diagram { position: absolute; left: 600px; top: 300px; }
  .diagram text { font-family: "Merriweather", serif; font-weight: 300; fill: var(--slate-text); }
  .diagram .small { font-family: "Open Sans", sans-serif; font-size: 8.4px; fill: #666; }
</style>
</head>
<body>
<div class="canvas">
  <div class="panel-right"></div>
  <div class="spread"></div>
  <div class="fold"></div>

  <div class="portrait" role="img" aria-label="Portrait photo of the founding principal in an office"></div>
  <div class="title-bar">What Makes BWC Unique</div>

  <div class="intro">
    <p><span class="dropcap">W</span>e understand that wealth and families is very complex. As families try to transfer wealth it can be an incredible blessing or, if done improperly, can be incredibly destructive. Often a neutral third party is needed to come alongside the family's advisory team to provide guidance as families go through their wealth transition.</p>
    <p>Our relational focus, and Open Framework<sup style="font-size:6px">tm</sup> approach, helps families to successfully navigate through the complexities of wealth, family and trusts. We believe a family "legacy" is about more than just money.</p>
  </div>
  <div class="signature"><strong>Daniel Harlow, J.D.</strong>Founding Principal</div>

  <div class="qualities">
    <div class="quality"><h3>Responsive</h3><p>The family deals directly with decision makers instead of being subject to committees with whom the family may never have the opportunity to interact or engage.</p></div>
    <div class="quality"><h3>Family Focus</h3><p>We help families successfully navigate the complexities of family wealth, not just perform trust administration.</p></div>
    <div class="quality"><h3>Independent</h3><p>To avoid any conflicts of interest, we have no formal affiliations with wealth management firms or financial advisory practices.</p></div>
    <div class="quality"><h3>Customized</h3><p>Together we develop a customized approach that will best suit the family's needs.</p></div>
    <div class="quality"><h3>Collaborative</h3><p>We work collaboratively with the family's team of trusted professionals.</p></div>
  </div>

  <div class="band">
    <div class="org">Brightwell Custody Group</div>
    <div class="team">Client/Family Centered Team</div>
  </div>

  <svg class="diagram" width="598" height="498" viewBox="600 300 598 498">
    <g stroke="var(--tan)" stroke-width="3" fill="none">
      <line x1="747" y1="496" x2="808" y2="496"/>
      <line x1="992" y1="496" x2="1052" y2="496"/>
      <line x1="855" y1="578" x2="805" y2="625"/>
      <line x1="945" y1="578" x2="997" y2="625"/>
    </g>
    <g stroke="var(--tan)" stroke-width="3" fill="#fff">
      <circle cx="687" cy="496" r="60"/>
      <circle cx="1112" cy="496" r="60"/>
      <circle cx="763" cy="668" r="60"/>
      <circle cx="1039" cy="668" r="60"/>
      <circle cx="901" cy="713" r="60"/>
    </g>
    <circle cx="817" cy="372" r="59" fill="var(--photo-warm)" stroke="var(--tan)" stroke-width="3" role="img" aria-label="Photo of a smiling woman"/>
    <circle cx="986" cy="372" r="59" fill="#ece8e4" stroke="var(--tan)" stroke-width="3" role="img" aria-label="Photo of two smiling children"/>
    <polygon points="855,417 945,417 992,497 945,578 855,578 808,497" fill="#e6dbd1" stroke="var(--tan)" stroke-width="3" role="img" aria-label="Photo of a smiling senior couple"/>
    <text x="687" y="503" font-size="18" text-anchor="middle">Attorney</text>
    <text x="1112" y="503" font-size="18" text-anchor="middle">Accountant</text>
    <text x="763" y="675" font-size="18" text-anchor="middle">Financial</text>
    <text x="1039" y="675" font-size="18" text-anchor="middle">Trustee</text>
    <text x="901" y="691" font-size="12" text-anchor="middle">Human Capital</text>
    <text x="901" y="707" font-size="12" text-anchor="middle">Resources</text>
    <text class="small" x="901" y="725" text-anchor="middle">Legacy Development</text>
    <text class="small" x="901" y="736" text-anchor="middle">Health Care Management</text>
    <text class="small" x="901" y="747" text-anchor="middle">Philanthropic Services</text>
    <text class="small" x="901" y="758" text-anchor="middle">Life Coaching</text>
  </svg>
</div>
</body>
</html>
```